Q Linkora

Ned a new business card, need two designs one to be for communications and one to be for security.
Communications will have what we do on it which include:-
PABX systems
Data Cabling
Phone services
Fibre
Security
"your communications specialist in the Pilbara"
The Severity one will have on it:-
CCTV
Alarm
Access control
Security consulting
Communications services
"Your security partner in the Pilbara"
Target Market(s)
industry
Industry/Entity Type
Communications
Contact Information for Business Card
Marcus Delbrook
0427350912
marcus@qlinkora.com.au
www.qlinkora.com.au

```html
<!DOCTYPE html>
<html lang="en">
<head>
<meta charset="utf-8">
<title>Q Linkora – Business Cards</title>
<link rel="stylesheet" href="https://fonts.googleapis.com/css2?family=PT+Sans:ital,wght@0,400;0,700;1,400&display=swap">
<style>
  :root {
    --backdrop: #2b2622;
    --card: #141414;
    --card-edge: #1d1d1d;
    --accent: #f2a22c;
    --text-light: #e9e9e9;
    --text-muted: #8d8d8d;
    --divider: #3a3a3a;
  }
  * { box-sizing: border-box; margin: 0; padding: 0; }
  html, body {
    width: 1200px; height: 844px; overflow: hidden;
    background: var(--backdrop);
    font-family: "PT Sans", "Helvetica Neue", Arial, sans-serif;
  }
  .stage {
    position: relative; width: 1200px; height: 844px;
    display: flex; align-items: center; justify-content: center; gap: 60px;
  }
  .card {
    position: relative; width: 520px; height: 297px;
    background: var(--card);
    border: 1px solid var(--card-edge);
    border-radius: 3px;
    box-shadow: 0 18px 40px rgba(0,0,0,.45);
    color: var(--text-light);
  }
  .brand {
    display: flex; align-items: center; gap: 10px;
    color: var(--accent); font-weight: 700; font-size: 46px;
    letter-spacing: 0.5px; line-height: 1;
  }
  .brand-dot {
    width: 14px; height: 14px; border-radius: 50%;
    background: var(--accent);
  }

  /* Front */
  .card-front .brand { position: absolute; left: 150px; top: 52px; }
  .person {
    position: absolute; left: 40px; top: 160px; width: 210px; text-align: right;
  }
  .person-name { color: var(--accent); font-weight: 700; font-size: 24px; }
  .person-role { color: var(--text-muted); font-size: 16px; margin-top: 2px; }
  .person-address { color: var(--text-muted); font-size: 17px; line-height: 1.2; margin-top: 16px; }
  .front-divider {
    position: absolute; left: 268px; top: 160px; width: 1px; height: 100px;
    background: var(--divider);
  }
  .contacts {
    position: absolute; left: 285px; top: 158px; list-style: none;
  }
  .contact-item {
    display: flex; align-items: center; gap: 10px;
    color: var(--text-muted); font-size: 16px; height: 26px;
  }
  .contact-icon {
    width: 18px; height: 18px; border-radius: 2px; background: var(--accent);
    display: flex; align-items: center; justify-content: center; flex: none;
  }

  /* Back */
  .card-back { text-align: center; }
  .card-back .brand { justify-content: center; margin-top: 72px; }
  .services { margin-top: 38px; font-size: 17px; line-height: 1.3; color: var(--text-light); }
  .services .sep { color: var(--accent); padding: 0 3px; }
  .tagline { margin-top: 8px; color: var(--accent); font-size: 17px; }
</style>
</head>
<body>
<main class="stage">

  <section class="card card-front" aria-label="Business card front">
    <div class="brand"><span class="brand-dot"></span>qlinkora</div>

    <div class="person">
      <p class="person-name">Marcus Delbrook</p>
      <p class="person-role">Managing Director</p>
      <p class="person-address">14 Harbour Road<br>Port Hedland WA 6721</p>
    </div>

    <div class="front-divider"></div>

    <ul class="contacts">
      <li class="contact-item">
        <span class="contact-icon">
          <svg width="12" height="12" viewBox="0 0 12 12"><path d="M2.5 1h2l1 2.5-1.3.9a6 6 0 0 0 3.4 3.4l.9-1.3 2.5 1v2a1 1 0 0 1-1 1A9 9 0 0 1 1.5 2a1 1 0 0 1 1-1z" fill="#141414"/></svg>
        </span>0427350912
      </li>
      <li class="contact-item">
        <span class="contact-icon">
          <svg width="12" height="12" viewBox="0 0 12 12"><rect x="3" y="0.5" width="6" height="11" rx="1" fill="#141414"/><rect x="4" y="1.8" width="4" height="7" fill="#f2a22c"/></svg>
        </span>(08) 9140 2317
      </li>
      <li class="contact-item">
        <span class="contact-icon">
          <svg width="12" height="12" viewBox="0 0 12 12"><rect x="1" y="2.5" width="10" height="7" rx="0.8" fill="#141414"/><path d="M1.5 3l4.5 3.5L10.5 3" stroke="#f2a22c" stroke-width="1" fill="none"/></svg>
        </span>marcus@qlinkora.com.au
      </li>
      <li class="contact-item">
        <span class="contact-icon">
          <svg width="12" height="12" viewBox="0 0 12 12"><path d="M6 11.5S2 7 2 4.5a4 4 0 0 1 8 0C10 7 6 11.5 6 11.5z" fill="#141414"/><circle cx="6" cy="4.5" r="1.4" fill="#f2a22c"/></svg>
        </span>www.qlinkora.com.au
      </li>
    </ul>
  </section>

  <section class="card card-back" aria-label="Business card back">
    <div class="brand"><span class="brand-dot"></span>qlinkora</div>
    <p class="services">
      CCTV<span class="sep">|</span>Alarm<span class="sep">|</span>Access control<br>
      Security Consulting<span class="sep">|</span>Communications services
    </p>
    <p class="tagline">"Your security partner in the Pilbara"</p>
  </section>

</main>
</body>
</html>
```